Consulting company business cards

We have a base design, but would be willing to update. We have a new logo/"tag" that needs to be added. Current business card design is attached for reference into our "style."

Industry/Entity Type

Business

Contact Information for Business Card

Should contain name and title, office number, mobile number if appropriate, e-mail, website, physical address, and company logo.

Font styles to use
Other font styles liked:
• See current card design on KorvandBCard

Colors
0455a3
85acd3
aaaaaa

Requirements
Must have
• Our colors are navy blue, gray, and a lighter blue
Nice to have
• Design that I can easily drop in new names/titles as we hire employees.

```html
<!DOCTYPE html>
<html lang="en">
<head>
<meta charset="utf-8">
<title>Brenlow Business Cards</title>
<link rel="stylesheet" href="https://fonts.googleapis.com/css2?family=Open+Sans:wght@400;600;700&display=swap">
<style>
  :root {
    --navy: #0a3350;
    --light-blue: #7eaec8;
    --white: #ffffff;
    --backdrop: #e9e7e4;
    --text-on-navy: #ffffff;
  }
  * { box-sizing: border-box; margin: 0; padding: 0; }
  html, body {
    width: 1200px; height: 900px; overflow: hidden;
    background: var(--backdrop);
    font-family: "Open Sans", Arial, sans-serif;
  }
  .stage { position: relative; width: 1200px; height: 900px; }
  .card {
    position: absolute;
    width: 587px; height: 362px;
    overflow: hidden;
    box-shadow: 0 6px 18px rgba(0,0,0,0.18);
  }
  .card-front { left: 78px; top: 35px; background: var(--white); }
  .card-back { left: 388px; top: 505px; width: 567px; height: 352px; background: var(--navy); }

  .card-shapes { position: absolute; inset: 0; }

  .brand { position: absolute; display: flex; flex-direction: column; align-items: flex-start; }
  .brand-row { display: flex; align-items: center; gap: 12px; }
  .brand-name {
    font-weight: 700; font-size: 58px; line-height: 1;
    letter-spacing: 2px; text-transform: uppercase;
  }
  .brand-dot { width: 44px; height: 44px; border-radius: 50%; }
  .brand-tagline {
    font-size: 15px; letter-spacing: 1.6px; text-transform: uppercase;
    margin-top: 6px;
  }
  .card-front .brand { left: 140px; top: 50px; }
  .card-front .brand-name { color: var(--navy); }
  .card-front .brand-dot { background: var(--light-blue); }
  .card-front .brand-tagline { color: var(--navy); }

  .card-back .brand { left: 130px; top: 128px; }
  .card-back .brand-name { color: var(--light-blue); }
  .card-back .brand-dot { background: var(--light-blue); }
  .card-back .brand-tagline { color: var(--light-blue); }

  .person {
    position: absolute; right: 306px; top: 242px;
    text-align: right; color: var(--text-on-navy);
  }
  .person-name { font-weight: 600; font-size: 18px; line-height: 24px; }
  .person-title { font-size: 14.5px; line-height: 20px; margin-bottom: 8px; }
  .person-address { font-size: 14.5px; line-height: 21px; }

  .divider {
    position: absolute; left: 300px; top: 222px;
    width: 1px; height: 114px; background: rgba(255,255,255,0.35);
  }

  .contact-list {
    position: absolute; left: 316px; top: 251px;
    list-style: none; color: var(--text-on-navy);
    font-size: 14.5px; line-height: 21.5px;
  }
  .contact-item { display: flex; align-items: center; gap: 6px; }
  .contact-icon { width: 11px; height: 11px; flex: none; fill: var(--text-on-navy); }
</style>
</head>
<body>
<main class="stage">

  <section class="card card-front" aria-label="Business card front">
    <svg class="card-shapes" width="587" height="362" viewBox="0 0 587 362" aria-hidden="true">
      <polygon points="0,178 397,178 382,203 0,203" fill="var(--light-blue)"/>
      <polygon points="0,205 385,205 414,170 587,170 587,362 0,362" fill="var(--navy)"/>
    </svg>

    <div class="brand">
      <div class="brand-row">
        <span class="brand-name">Brenlow</span>
        <span class="brand-dot"></span>
      </div>
      <span class="brand-tagline">A Cloud Consulting Company</span>
    </div>

    <div class="person">
      <p class="person-name">Renata Korvand</p>
      <p class="person-title">Managing Director</p>
      <p class="person-address">4310 N 18 th lakeview<br>ohio 43120</p>
    </div>

    <span class="divider"></span>

    <ul class="contact-list">
      <li class="contact-item">
        <svg class="contact-icon" viewBox="0 0 12 12"><path d="M1 4c0-2 2-3 5-3s5 1 5 3v1H8V4H4v1H1zM2 6h8l1 5H1z"/></svg>
        555.014.2210
      </li>
      <li class="contact-item">
        <svg class="contact-icon" viewBox="0 0 12 12"><path d="M2 3h8v8H2zM4 0h4v3H4zM4 5h4v1H4zM4 7h4v1H4z"/></svg>
        555.014.2271
      </li>
      <li class="contact-item">
        <svg class="contact-icon" viewBox="0 0 12 12"><path d="M1 3h10v7H1zM1 3l5 4 5-4" stroke="var(--navy)" stroke-width="0.8"/></svg>
        rkorvand@brenlowtech.com
      </li>
      <li class="contact-item">
        <svg class="contact-icon" viewBox="0 0 12 12"><circle cx="6" cy="6" r="5.5"/><path d="M1 6h10M6 0.5c-2.5 3-2.5 8 0 11M6 0.5c2.5 3 2.5 8 0 11" stroke="var(--navy)" stroke-width="0.8" fill="none"/></svg>
        www.brenlowtech.com
      </li>
    </ul>
  </section>

  <section class="card card-back" aria-label="Business card back">
    <div class="brand">
      <div class="brand-row">
        <span class="brand-name">Brenlow</span>
        <span class="brand-dot"></span>
      </div>
      <span class="brand-tagline">A Cloud Consulting Company</span>
    </div>
  </section>

</main>
</body>
</html>
```